Bref créative
findnearby-hub.com - creative brochure
findnearby-hub.com
Visit our website - findnearby-hub.com
Internet Services
Brick and mortar local businesses
The brochure needs to demonstrate confidence, affordability, and exclusivity.
The text for the brochure can be found on the website findnearby-hub.com
The design can be a 3 fold or rack card style… whatever turns out best

```html
<!DOCTYPE html>
<html lang="en">
<head>
<meta charset="utf-8">
<title>findnearby-hub.com brochure</title>
<link href="https://fonts.googleapis.com/css2?family=Open+Sans:wght@400;600;700;800&display=swap" rel="stylesheet">
<style>
:root{
  --red:#c9202b;
  --ink:#3a3a3a;
  --ink-soft:#555;
  --paper:#f4f4f4;
  --card:#e9e9e9;
  --card-edge:#cfcfcf;
  --header:#2e2e2e;
  --white:#fff;
  --blue:#3d6fb6;
}
*{margin:0;padding:0;box-sizing:border-box}
html,body{width:1200px;height:932px;overflow:hidden;background:var(--paper)}
body{font-family:"Open Sans",Arial,sans-serif;color:var(--ink)}
.brochure{position:relative;width:1200px;height:932px;background:linear-gradient(180deg,#fafafa,#ececec);overflow:hidden}
.panel{position:absolute;top:0;height:932px}
.panel-left{left:0;width:400px}
.panel-mid{left:400px;width:400px}
.panel-right{left:800px;width:400px}
.art{position:absolute;border-radius:6px}
.map-art{left:14px;top:30px;width:156px;height:156px;background:linear-gradient(135deg,#d9dcd2,#b9bfb2)}
.intro{position:absolute;left:182px;top:28px;width:205px;font-size:15px;line-height:1.38;color:var(--ink-soft)}
.lead{position:absolute;left:14px;top:214px;width:372px;font-size:14.5px;line-height:1.4;color:var(--ink-soft)}
.ribbon{position:absolute;left:0;height:40px;background:var(--red);color:var(--white);font-weight:800;font-size:17px;line-height:40px;padding-left:14px;white-space:nowrap}
.ribbon::after{content:"";position:absolute;right:-20px;top:0;border-left:20px solid var(--red);border-top:20px solid transparent;border-bottom:20px solid transparent}
.ribbon-help{top:346px;width:354px}
.ribbon-services{top:640px;width:190px;font-size:18px}
.benefits{position:absolute;left:16px;top:422px;list-style:none}
.benefits li{display:flex;align-items:center;gap:10px;font-weight:800;font-size:14px;height:33px;color:#333;white-space:nowrap}
.services-text{position:absolute;left:14px;top:730px;width:372px;font-size:14.5px;line-height:1.45;color:var(--ink-soft)}
.search-word{position:absolute;left:120px;top:22px;font-size:46px;font-weight:800;color:var(--blue);letter-spacing:-1px}
.search-bar{position:absolute;left:30px;top:96px;width:340px;height:22px;border:2px solid #888;border-radius:3px;background:var(--white)}
.search-bar::after{content:"";position:absolute;right:0;top:0;width:54px;height:100%;background:#555}
.card{position:absolute;background:var(--card);border:1px solid var(--card-edge);border-radius:6px;box-shadow:0 3px 8px rgba(0,0,0,.18)}
.card-head{background:var(--header);color:var(--white);font-weight:800;font-size:25px;height:54px;line-height:54px;padding-left:20px;margin:14px 0 0 -8px;width:calc(100% + 16px);border-radius:4px;white-space:nowrap}
.card-body{padding:16px 20px 0;font-size:13.5px;line-height:1.42;color:var(--ink-soft)}
.card-body p{margin-bottom:14px}
.card-body .cta{color:var(--red);font-weight:700}
.card-body strong{color:var(--red)}
.card-search{left:20px;top:174px;width:360px;height:420px}
.features-head{position:absolute;left:22px;top:606px;background:var(--red);color:var(--white);font-weight:800;font-size:28px;padding:2px 16px;border-radius:4px;letter-spacing:1px}
.features{position:absolute;left:26px;top:690px;list-style:none;font-size:10.5px;font-weight:700;line-height:16px;color:#333;white-space:nowrap}
.features li::before{content:"■";color:var(--red);font-size:7px;margin-right:6px;vertical-align:2px}
.keys-art{left:90px;top:24px;width:240px;height:110px;background:linear-gradient(180deg,#eeeeee,#c9c9c9)}
.solution{position:absolute;left:0;width:400px;top:148px;text-align:center;color:var(--red);font-size:22px;letter-spacing:9px;font-weight:600}
.card-location{left:22px;top:240px;width:360px;height:404px}
.houses-art{left:20px;top:670px;width:370px;height:262px;border-radius:6px 6px 0 0;background:linear-gradient(180deg,#e2e2e2,#9a9a9a)}
</style>
</head>
<body>
<main class="brochure">
  <section class="panel panel-left">
    <div class="art map-art" role="img" aria-label="Illustration of a street map with a location pin"></div>
    <p class="intro">As the Internet evolves and web users become more sophisticated, local consumers are turning more and more to the Internet to find products and services on a local basis.</p>
    <p class="lead">We'll get your website listed in Seekly places, Findr and Lookabout local for amazing local visibility. Everytime a local consumer searches for your product or service, you'll be there in perfect view.</p>
    <div class="ribbon ribbon-help">WE CAN HELP YOUR BUSINESS...</div>
    <ul class="benefits">
      <li><svg width="18" height="18" viewBox="0 0 18 18"><path d="M2 9l5 5L16 3" fill="none" stroke="#c9202b" stroke-width="3"/></svg>ELIMINATE PAY PER CLICK CHARGES</li>
      <li><svg width="18" height="18" viewBox="0 0 18 18"><path d="M2 9l5 5L16 3" fill="none" stroke="#c9202b" stroke-width="3"/></svg>ENHANCE YOUR LOCAL SEARCH LISTINGS</li>
      <li><svg width="18" height="18" viewBox="0 0 18 18"><path d="M2 9l5 5L16 3" fill="none" stroke="#c9202b" stroke-width="3"/></svg>REDUCE YOUR ADVERTISING BUDGET</li>
      <li><svg width="18" height="18" viewBox="0 0 18 18"><path d="M2 9l5 5L16 3" fill="none" stroke="#c9202b" stroke-width="3"/></svg>INCREASE PROFITS</li>
      <li><svg width="18" height="18" viewBox="0 0 18 18"><path d="M2 9l5 5L16 3" fill="none" stroke="#c9202b" stroke-width="3"/></svg>ACQUIRE NEW CUSTOMERS</li>
      <li><svg width="18" height="18" viewBox="0 0 18 18"><path d="M2 9l5 5L16 3" fill="none" stroke="#c9202b" stroke-width="3"/></svg>GAIN VISIBILITY OVER YOUR COMPETITION</li>
    </ul>
    <div class="ribbon ribbon-services">OUR SERVICES</div>
    <p class="services-text">We specialize in getting localized results in the search engines i.e., if you are an appliance repair company in Cedarbrook, BC you will want us... your LOCAL SEO experts to establish your presence to capture all the local customers searching specifically for your products or services.</p>
  </section>

  <section class="panel panel-mid">
    <div class="search-word">Search</div>
    <div class="search-bar"></div>
    <article class="card card-search">
      <h2 class="card-head">SEARCH + LOCAL</h2>
      <div class="card-body">
        <p>Optimizing your local listings and ranking it to the top of local keyword searches is essential to your business!</p>
        <p>It's been proven over and over that local clients who buy our <strong>FINDNEARBY-HUB.com</strong> services have had the best ROI (return on investment) then any other form of advertising by a mile!</p>
        <p>We know how to get your local listings to the top of local search queries no matter where your local business is located.</p>
        <p class="cta">Order our services today for guaranteed results</p>
      </div>
    </article>
    <h2 class="features-head">FEATURES</h2>
    <ul class="features">
      <li>Complete Website SEO Analysis</li>
      <li>Seekly / Findr / Lookabout local listings</li>
      <li>Website tracking and analytics setup</li>
      <li>Listing Citations-Rateside / 411 / TownPages / Campaigns + more</li>
      <li>Business maps and directions for the customers</li>
      <li>Business profile for customer information</li>
      <li>Multiple languages</li>
      <li>Customer reviews</li>
      <li>Customer ratings</li>
      <li>Payment methods</li>
      <li>Photo galleries of the business</li>
      <li>Detailed monthly reporting</li>
      <li>Monthly monitoring and updates</li>
    </ul>
  </section>

  <section class="panel panel-right">
    <div class="art keys-art" role="img" aria-label="Illustration of a row of keys with one red key"></div>
    <div class="solution">SOLUTION</div>
    <article class="card card-location">
      <h2 class="card-head">LOCATION, LOCATION</h2>
      <div class="card-body">
        <p>In the brick-and-mortar world it has always been about the LOCATION.</p>
        <p>You can now dominate the location factor on a digital level to capture these local, targeted and hot prospects ahead of your competition!</p>
        <p>We know how to get your local listings to the top of search queries no matter where your local business is located.</p>
        <p class="cta">Order our exclusive services today for guaranteed results!</p>
      </div>
    </article>
    <div class="art houses-art" role="img" aria-label="Illustration of house silhouettes with a magnifying glass over one house"></div>
  </section>
</main>
</body>
</html>
```